brightquokka.net we need a webpage designed for our new product

We need a webpage designed for our new range of products from our new brand. We have had a logo designed on sketchharbor (see attached) and we want to keep to this theme. Our first product is a range of affordable app controlled LED lightbulbs.

I have added some photos that we think is good inspirational material and would be good as a background to this website, but we want the site to look modern but not conventional. We would like something that makes our company look quirky not corporate.

Thats it

Target Market(s)

Our product is being stocked by big name online retailers in the UK, the page will get link through hits from our app. Our target market is gadget freaks of all ages.

Industry/Entity Type

It Company

Requirements
Must have
• We are going to need a help page, text to be uploaded next few days.

We need a contact page.

design my work on iOS and Android as most people will access page through their handset or tablet.
Should not have
• We do not want anything too corporate.

```html
<!DOCTYPE html>
<html lang="en">
<head>
<meta charset="utf-8">
<title>Bright Quokka – Home</title>
<link rel="stylesheet" href="https://fonts.googleapis.com/css2?family=Open+Sans:ital,wght@0,400;0,600;1,400;1,600&family=Satisfy&display=swap">
<style>
:root{
  --green:#3f9b35;
  --green-bright:#46a93a;
  --heading-green:#3b9a38;
  --text:#555555;
  --nav-darker:#3c3c3c;
  --btn-dark:#555555;
  --line:#dddddd;
  --footer:#565656;
  --white:#ffffff;
}
*{box-sizing:border-box;margin:0;padding:0}
html,body{width:1154px;height:1200px;overflow:hidden}
body{position:relative;font-family:"Open Sans",Arial,sans-serif;color:var(--text);background:#111}
.backdrop{position:absolute;left:0;top:0;width:1154px;height:1084px;
  background:linear-gradient(180deg,rgba(0,0,0,0) 0%,rgba(0,0,0,.15) 45%,rgba(0,0,0,.85) 75%,#000 100%),
  linear-gradient(90deg,#6b4a32 0%,#8a6a4e 12%,#3a2a20 14%,#5b4536 86%,#a08a74 90%,#6a5240 100%);}
.page{position:absolute;left:115px;top:38px;width:923px;height:1030px;background:var(--white);border-radius:3px}
.abs{position:absolute}
.brand{left:19px;top:10px;width:130px;height:200px}
.brand-dot{position:absolute;left:30px;top:24px;width:50px;height:50px;border-radius:50%;background:var(--green)}
.brand-name{position:absolute;left:0;top:146px;font-size:9px;font-weight:600;letter-spacing:.4px;color:var(--green);white-space:nowrap}
.util{right:10px;top:22px;font-size:12px;color:#666}
.util a{color:#666;text-decoration:none}
.util span{margin:0 7px}
.search{left:657px;top:67px;width:256px;height:35px;display:flex}
.search-input{flex:1;border:1px solid #d4d4d4;border-right:0;background:#f7f7f7;font-size:12px;font-style:italic;color:#999;padding:9px 10px}
.search-btn{width:41px;background:var(--green);display:flex;align-items:center;justify-content:center}
.nav{left:163px;top:121px;width:750px;height:44px;display:flex;background:linear-gradient(#555,var(--nav-darker));border-radius:2px}
.nav a{color:#fff;text-decoration:none;font-size:14px;font-weight:600;display:flex;align-items:center;justify-content:center;height:100%}
.nav a.active{background:var(--green-bright)}
.hero{left:10px;top:172px;width:904px;height:386px;border-radius:3px;overflow:hidden;
  background:radial-gradient(circle at 60% 10%,#c4dc2a 0%,#8ec22a 35%,#5a9a22 70%,#3e7a1a 100%)}
.hero-photo{position:absolute;left:520px;top:0;width:384px;height:386px;
  background:radial-gradient(ellipse 55% 50% at 50% 45%,rgba(235,240,225,.55) 0%,rgba(90,100,90,.35) 55%,rgba(0,0,0,0) 100%)}
.hero h1{position:absolute;left:52px;top:100px;font-size:27px;font-weight:600;color:#fff;white-space:nowrap}
.hero p{position:absolute;left:52px;top:148px;width:420px;font-size:16px;line-height:23px;font-weight:600;color:#1f3a0a}
.btn-light{position:absolute;left:52px;top:230px;width:164px;height:50px;background:linear-gradient(#fff,#e4e4e4);border-radius:3px;font-size:16px;font-weight:600;color:#333;display:flex;align-items:center;justify-content:center}
.store-badge{position:absolute;left:235px;top:230px;width:150px;height:50px;background:#111;border:1px solid #777;border-radius:6px}
.dots{position:absolute;left:52px;top:342px;display:flex;gap:6px}
.dots i{width:12px;height:12px;border-radius:3px;background:#fff}
.dots i:first-child{background:#444}
.app-note{position:absolute;left:219px;top:334px;font-family:"Satisfy",cursive;font-size:18px;font-style:italic;color:#fff;white-space:nowrap}
.app-arrow{position:absolute;left:356px;top:290px}
.heading{font-size:24px;font-weight:400;color:var(--heading-green);white-space:nowrap}
.copy{font-size:13px;line-height:22px;color:var(--text)}
.quote{font-style:italic;width:262px}
.qmark{display:inline-block;font-size:28px;font-weight:600;font-style:normal;color:#999;line-height:10px;vertical-align:-8px}
.btn-dark{position:absolute;height:35px;background:var(--btn-dark);color:#fff;font-size:12px;font-weight:600;border-radius:2px;display:flex;align-items:center;justify-content:center}
.vline{position:absolute;width:1px;background:var(--line)}
.hline{position:absolute;height:1px;background:var(--line)}
.thumb{position:absolute;top:631px;width:162px;height:104px;border:2px solid #e2e2e2}
.arrows{position:absolute;display:flex;gap:10px}
.footer{position:absolute;left:0;top:1084px;width:1154px;height:116px;background:var(--footer);color:#eee}
.footer-nav{position:absolute;left:124px;top:18px;display:flex;gap:24px;font-size:12px}
.copyright{position:absolute;left:124px;top:55px;font-size:11px;line-height:16px;color:#ddd}
.copyright em{font-style:normal;color:var(--green-bright)}
.foot-title{position:absolute;top:16px;font-size:15px;font-weight:600;color:#fff}
.email{position:absolute;left:665px;top:47px;width:156px;height:27px;background:#fff;color:#888;font-size:12px;padding:5px 10px}
.email-btn{position:absolute;left:821px;top:47px;width:29px;height:27px;background:var(--green-bright);display:flex;align-items:center;justify-content:center}
.social{position:absolute;top:47px;width:27px;height:27px;border-radius:3px;background:#777}
</style>
</head>
<body>
<div class="backdrop" role="img" aria-label="Photo of a vintage lighting store with hanging lamps and shades"></div>

<div class="page">
  <div class="abs brand"><span class="brand-dot"></span><span class="brand-name">BRIGHTQUOKKA.NET</span></div>

  <div class="abs util"><a href="#">Log in</a><span>|</span><a href="#">Register</a><span>|</span><a href="#">FAQ</a><span>|</span><a href="#">Newsletter SignUp</a></div>

  <div class="abs search">
    <div class="search-input">Search keywords..</div>
    <div class="search-btn"><svg width="18" height="18" viewBox="0 0 18 18"><circle cx="7" cy="7" r="5" fill="none" stroke="#fff" stroke-width="2.2"/><line x1="11" y1="11" x2="16" y2="16" stroke="#fff" stroke-width="3" stroke-linecap="round"/></svg></div>
  </div>

  <nav class="abs nav">
    <a class="active" style="width:88px">Home</a>
    <a style="width:104px">About Us</a>
    <a style="width:102px">Products</a>
    <a style="width:106px">Services</a>
    <a style="width:76px">Blog</a>
    <a style="width:136px">Testimonials</a>
    <a style="width:138px">Contact Us</a>
  </nav>

  <section class="abs hero">
    <div class="hero-photo" role="img" aria-label="Product photo of an LED lightbulb"></div>
    <h1>Morbi iaculis fringilla gravida</h1>
    <p>Aenean a nibh eget turpis vehicula tempus ac sed massa. Vestibulum dolor nulla, ultrices ac tincidunt sed, laoreet non est.</p>
    <div class="btn-light">VIEW PRODUCTS</div>
    <div class="store-badge" aria-label="App download badge"></div>
    <div class="dots"><i></i><i></i><i></i><i></i></div>
    <div class="app-note">Download Our App</div>
    <svg class="app-arrow" width="30" height="64" viewBox="0 0 30 64"><path d="M2 60 Q22 54 23 32 Q24 16 12 6" fill="none" stroke="#fff" stroke-width="1.3"/><path d="M6 12 L12 5 L16 13" fill="none" stroke="#fff" stroke-width="1.3"/></svg>
  </section>

  <h2 class="abs heading" style="left:10px;top:582px">Welcome to Our Website</h2>
  <p class="abs copy" style="left:10px;top:626px;width:345px">Aliquam molestie, mi et imperdiet euismod, dui purus auctor tellus, et interdum lacus lectus et ante. Sed accumsan sollicitudin sapien, sit amet adipiscing turpis gravida ac. In congue, neque ac lobortis volutpat, libero mauris varius mi, vitae suscipit ipsum ligula vitae risus.</p>
  <div class="btn-dark" style="left:10px;top:761px;width:104px">Read More</div>

  <div class="vline" style="left:375px;top:592px;height:210px"></div>

  <h2 class="abs heading" style="left:395px;top:582px">Product Range</h2>
  <div class="arrows" style="left:887px;top:592px">
    <svg width="12" height="16" viewBox="0 0 12 16"><path d="M9 2 L3 8 L9 14" fill="none" stroke="#333" stroke-width="1.6"/></svg>
    <svg width="12" height="16" viewBox="0 0 12 16"><path d="M3 2 L9 8 L3 14" fill="none" stroke="#333" stroke-width="1.6"/></svg>
  </div>
  <div class="thumb" style="left:395px;background:radial-gradient(circle at 55% 50%,#c8d9a8,#9cc44a)" role="img" aria-label="Photo of an LED bulb on green"></div>
  <div class="thumb" style="left:573px;background:radial-gradient(circle at 50% 50%,#eaeaea,#fff)" role="img" aria-label="Photo of a clear multi-LED bulb"></div>
  <div class="thumb" style="left:751px;background:radial-gradient(circle at 40% 45%,#d8e4ee,#2a7cc0)" role="img" aria-label="Photo of two LED bulbs on blue"></div>
  <div class="btn-dark" style="left:780px;top:761px;width:134px">View All Products</div>

  <div class="hline" style="left:10px;top:822px;width:904px"></div>

  <div class="abs" style="left:10px;top:842px;width:174px;height:167px;background:linear-gradient(160deg,#a8856a,#e8dccc 50%,#c49a78)" role="img" aria-label="Photo of a hand fitting a bulb into a ceiling lamp"></div>
  <h2 class="abs heading" style="left:207px;top:832px">Services</h2>
  <p class="abs copy" style="left:208px;top:868px;width:405px">Aliquam molestie, mi et imperdiet euismod, dui purus auctor tellus, et interdum lacus lectus et ante. Sed accumsan sollicitudin sapien, sit amet adipiscing turpis gravida ac. In congue, neque ac lobortis volutpat, libero mauris varius m..</p>
  <div class="btn-dark" style="left:208px;top:973px;width:104px">Read More</div>

  <div class="vline" style="left:627px;top:842px;height:167px"></div>

  <h2 class="abs heading" style="left:650px;top:832px">Client Says..</h2>
  <div class="arrows" style="left:880px;top:843px">
    <svg width="12" height="16" viewBox="0 0 12 16"><path d="M9 2 L3 8 L9 14" fill="none" stroke="#333" stroke-width="1.6"/></svg>
    <svg width="12" height="16" viewBox="0 0 12 16"><path d="M3 2 L9 8 L3 14" fill="none" stroke="#333" stroke-width="1.6"/></svg>
  </div>
  <p class="abs copy quote" style="left:650px;top:868px"><span class="qmark">&ldquo;</span> Aliquam molestie, mi et imperdiet euismod, dui purus auctor tellus, et interdum lacus lectus et ante. Sed accumsan sollicitudin sapien, sit amet adipiscing turpis gravida ac... <span class="qmark">&rdquo;</span></p>
  <div class="abs" style="left:650px;top:990px;font-size:13px;font-style:italic;font-weight:600;color:var(--heading-green)">-Mara Fenwick</div>
</div>

<footer class="footer">
  <div class="footer-nav"><span>Home</span><span>About Us</span><span>Products</span><span>Services</span><span>Blog</span><span>Testimonials</span><span>Contact Us</span></div>
  <div class="copyright">Copyright © 2014. <em>Bright Quokka.</em><br>All Right Reserved</div>
  <div class="foot-title" style="left:665px">Newsletter Signup</div>
  <div class="email">Enter Email</div>
  <div class="email-btn"><svg width="12" height="14" viewBox="0 0 12 14"><path d="M3 2 L9 7 L3 12" fill="none" stroke="#fff" stroke-width="2.5"/></svg></div>
  <div class="foot-title" style="left:894px">Connect Us</div>
  <div class="social" style="left:895px" aria-label="Social link"></div>
  <div class="social" style="left:932px" aria-label="Social link"></div>
  <div class="social" style="left:967px" aria-label="Social link"></div>
  <div class="social" style="left:1003px" aria-label="Social link"></div>
</footer>
</body>
</html>
```